Redesign company trifold brochure

We are rebranding our company in September and looking for a more professional design for our brochure.

What we do - providing interdisciplinary care for those supporting ill, elderly and special needs pets at home following the human hospice model of care - is very novel and our brochure is key in explaining it and our offerings.

We serve dogs and cats. Most of the animals are quite sick, elderly. I have many personal and stock photos we can use in the brochure. Please - no pictures of puppies and/or kittens.

The hard part is fitting the info and message into a clear and concise format.

It must be appealing both to pet owners and vets (who are our primary source of patients through referrals).

It should covey WARMTH, COMPASSION, PROFESSIONALISM, and EXPERTISE.

Please look at our website www.TrellisAnimalRespite.com for more info

We have until now used maroon and copper for colors - to reflect the "sunset" of the pets life. BUT are now changing to Navy, Teal and White to reflect calm, trust and competence.

We will use the same logo recolored.

Existing brochure and new logo are attached.

PLEASE ask questions!!
Updates

We have a library of stock images you are welcome to use. All have been legally acquired and we have the right to use them. You DO NOT have to use them, just sending along in case you wish to. https://www.filecrate.example/sh/qk4vrm82zd1pyno/KLQ7Ztbn-Rrfx2mh9sWpYJ4Dc?dl=0

Our colors are NAVY, TEAL and WHITE. For your reference, the navy we use is 99/87/44/55 (CMYK) The Teal we use is 76/11/44/0 (CMYK) Thank you!

Designers -- pleaseuse pictures of older pets (no puppies or kittens). Below is a link to stock photos we own that would be appropriate for use in the brochure. https://www.filecrate.example/sh/w274m6t9pxkr5da/KLRn3GsfwlTVBXEPcq_8ZNj5u?dl=0 THANK YOU!

Designers -- I would VERY much like to include a photo of a pet in a wheel chair. I have personal photos as well as (purchased) stock photos for this purpose which can be found at http://lnk.example/TARHC-Pets-in-Wheelchairs Thank you!!

Today is the last day! Many of you have submitted beautiful designs and others are rolling in. I am so appreciative of your time and energy!! Please do not let the deadline pass without YOUR very BEST entry being submitted!! Thank you! - Miriam & All of us at Trellis Animal Respite & Home Care

Target Market(s)

Pet Owners and Veterinarians

Industry/Entity Type

Pet Care

Font styles to use
Serif

Colors
0455a3
33b8a4
ffffff

Requirements
Must have
• Our logo and information about our services. Pictures of pets. Our contact info. PLEASE NOTE: this is a 2 sided brochure. Please submit both inside and outside.
Should not have
• puppies, kittens - anything off message

```html
<!DOCTYPE html>
<html lang="en">
<head>
<meta charset="utf-8">
<title>Trellis Animal Respite &amp; Home Care – Trifold Outside</title>
<link rel="stylesheet" href="https://fonts.googleapis.com/css2?family=Marcellus&family=Lora:ital@1&family=Arimo&display=swap">
<style>
  :root {
    --navy: #0f1d45;
    --teal: #23a79a;
    --white: #ffffff;
    --ink: #1b2a3a;
    --stage: #efece8;
  }
  * { box-sizing: border-box; margin: 0; padding: 0; }
  html, body { width: 1200px; height: 943px; overflow: hidden; background: var(--stage); }
  .brochure {
    position: absolute; left: 35px; top: 35px; width: 1130px; height: 870px;
    background: var(--white); box-shadow: 0 2px 8px rgba(0,0,0,.18); overflow: hidden;
  }
  .panel { position: absolute; top: 0; height: 870px; }
  .panel--beliefs { left: 0; width: 373px; background: var(--teal); }
  .panel--contact { left: 373px; width: 379px; background: var(--white); }
  .panel--cover { left: 752px; width: 378px; background: var(--navy); }

  .photo { position: absolute; }
  .photo--companions { left: 0; top: 0; width: 373px; height: 410px;
    background: linear-gradient(160deg, #fbfbfb 0%, #e9ddd2 45%, #b57a4c 100%); }
  .photo--meadow { left: 0; top: 0; width: 379px; height: 410px;
    background: linear-gradient(170deg, #e3ecd0 0%, #c8d98e 40%, #9fc35a 100%); }
  .photo--resting { left: 0; top: 205px; width: 378px; height: 510px;
    background: linear-gradient(150deg, #e7b7ad 0%, #e5cdb8 45%, #d6b58e 75%, #c8708a 100%); }

  .spread-wave { position: absolute; left: 0; top: 280px; width: 752px; height: 150px; z-index: 1; }

  .beliefs { position: absolute; left: 13px; top: 383px; width: 360px; color: var(--ink); z-index: 2; }
  .beliefs__title { font-family: "Marcellus", serif; font-weight: 400; font-size: 27px; line-height: 32px; color: var(--navy); margin-bottom: 6px; letter-spacing: .3px; }
  .beliefs__list { list-style: none; font-family: "Marcellus", serif; font-size: 14.6px; line-height: 21.5px; }
  .beliefs__list li { position: relative; padding-left: 22px; margin-bottom: 15px; color: #1d2b3e; white-space: nowrap; }
  .beliefs__list li::before { content: "\27A2"; position: absolute; left: 0; top: 0; font-size: 11px; color: var(--navy); }

  .brand { display: flex; align-items: center; gap: 12px; font-family: "Marcellus", serif; color: var(--navy); }
  .brand__mark { width: 46px; height: 46px; border-radius: 50%; background: var(--teal); flex: none; }
  .brand__name { font-size: 22px; line-height: 25px; }
  .brand--contact { position: absolute; left: 58px; top: 585px; width: 280px; }
  .brand--cover { position: absolute; left: 60px; top: 38px; width: 280px; }

  .contact { position: absolute; left: 0; top: 685px; width: 379px; text-align: center;
    font-family: "Arimo", sans-serif; font-size: 13.5px; color: #111; line-height: 18px; }
  .contact p { margin-bottom: 9px; }
  .contact__rule { width: 352px; height: 1px; background: #333; margin: 4px auto 9px; }
  .social { display: flex; align-items: center; justify-content: center; gap: 6px; font-size: 15px; margin-bottom: 5px; }
  .social__mark { width: 14px; height: 14px; background: var(--teal); flex: none; }

  .cover-wave { position: absolute; left: 0; width: 378px; }
  .cover-wave--top { top: 0; height: 250px; }
  .cover-wave--bottom { top: 660px; height: 90px; }

  .cover__tagline { position: absolute; left: 0; top: 754px; width: 378px; text-align: center;
    font-family: "Marcellus", serif; font-weight: 400; font-size: 19.5px; line-height: 27px; color: var(--white); }
  .cover__sub { position: absolute; left: 0; top: 832px; width: 378px; text-align: center;
    font-family: "Lora", serif; font-style: italic; font-size: 18px; color: var(--white); }
</style>
</head>
<body>
<main class="brochure">
  <section class="panel panel--beliefs">
    <div class="photo photo--companions" role="img" aria-label="Photo of a dog and a cat lying side by side wearing red holiday hats"></div>
  </section>

  <section class="panel panel--contact">
    <div class="photo photo--meadow" role="img" aria-label="Photo of a pale Labrador sitting in a sunny meadow beside its owner"></div>
    <div class="brand brand--contact">
      <span class="brand__mark"></span>
      <span class="brand__name">Trellis Animal Respite &amp; Home Care</span>
    </div>
    <div class="contact">
      <p>Contact us (555) 302-TRAR</p>
      <p>info@TrellisAnimalRespite.com</p>
      <p>www.TrellisAnimalRespite.com</p>
      <p>48 Meadowlark Road,<br>Suite 12 Fernhill, Ma 01999</p>
      <div class="contact__rule"></div>
      <div class="social"><span class="social__mark"></span>TrellisAnimalRespite</div>
      <div class="social"><span class="social__mark"></span>TrellisRespite</div>
    </div>
  </section>

  <svg class="spread-wave" viewBox="0 0 752 150" preserveAspectRatio="none" aria-hidden="true">
    <path d="M0,50 C150,100 300,124 373,124 L373,150 L0,150 Z" fill="var(--teal)"/>
    <path d="M373,124 C480,128 640,110 752,62 L752,150 L373,150 Z" fill="var(--white)"/>
    <path d="M380,112 C520,108 650,62 752,10 L752,42 C680,78 560,112 420,114 Z" fill="var(--teal)"/>
    <path d="M0,40 C150,85 300,112 420,112 C560,112 680,78 752,40 L752,66 C680,100 560,128 420,128 C300,128 150,105 0,54 Z" fill="var(--navy)"/>
  </svg>

  <div class="beliefs">
    <h2 class="beliefs__title">We Believe</h2>
    <ul class="beliefs__list">
      <li>That animals are conscious beings, capable of<br>thought, feeling, emotion and choice.</li>
      <li>That each animal is an individual with his or<br>her unique needs and whishes.</li>
      <li>That all pets deserve to be pain-free.</li>
      <li>That the principles of human hospice and<br>palliative care are equally powerful when<br>applied to animals</li>
      <li>That an interdisciplinary team is essential to<br>addressing that needs of pets and their<br>families through aging and illness.</li>
      <li>That quality of life is subjective best evaluated<br>by the family who knows and loves the<br>animal.</li>
      <li>That there isn't are answer that is right for<br>every animal or every family</li>
    </ul>
  </div>

  <section class="panel panel--cover">
    <div class="photo photo--resting" role="img" aria-label="Photo of an elderly golden dog resting its head on a soft toy"></div>
    <svg class="cover-wave cover-wave--top" viewBox="0 0 378 250" preserveAspectRatio="none" aria-hidden="true">
      <path d="M0,0 H378 V195 C260,165 120,165 0,190 Z" fill="var(--white)"/>
      <path d="M0,190 C120,165 260,165 378,195 L378,212 C260,182 120,182 0,205 Z" fill="var(--teal)"/>
      <path d="M0,205 C120,182 260,182 378,212 L378,226 C260,200 120,198 0,228 Z" fill="var(--navy)"/>
    </svg>
    <svg class="cover-wave cover-wave--bottom" viewBox="0 0 378 90" preserveAspectRatio="none" aria-hidden="true">
      <path d="M0,55 C120,68 260,60 378,30 L378,90 L0,90 Z" fill="var(--navy)"/>
      <path d="M120,62 C220,66 310,50 378,26 L378,36 C300,62 210,74 120,62 Z" fill="var(--teal)"/>
    </svg>
    <div class="brand brand--cover">
      <span class="brand__mark"></span>
      <span class="brand__name">Trellis Animal Respite &amp; Home Care</span>
    </div>
    <h1 class="cover__tagline">Skilled Home Care for Ill, Elderly<br>and Special Needs Animals</h1>
    <p class="cover__sub">Compassionate Support for Families</p>
  </section>
</main>
</body>
</html>
```